Emerging automotive detailing business

I am starting a small automotive detailing business in hopes of becoming a well-known detailer to work on high end cars. I would like a card to reflect the high quality and time I put into my work. The name of the company is Bright Crest Detailing. I feel like it represents racecars getting off the line at the drag strip as well as an innuendo of "Up the Ladder". I do minor paint correction such as clay barring, multi-step buffing and polishing, waxing, hand washes, etc. I am always striving to learn more and improve my work. My goal is to have total customer satisfaction. This is a female run business but I do not want it to be very girly. Elegant is okay! I have pictures of my personal wrenfield attached, they do not need to be incorporated but if you can think of a cool way to use 1 or all of them, go for it!

Target Market(s)

Anyone that owns a vehicle. Preferably high end vehicles such as Valtori, Castellverde and Morvani but I will also happily work on any car, truck or suv no matter what brand.

Industry/Entity Type

Automotive

Contact Information for Business Card

Bright Crest Detailing
Mira Tolland
4175 Quenhollow Rd
Ashmere PA 17492
Cell phone- call/text- 717-555-0148
email- brightcrestdetails@maildrop-example.com
Instagram: @brightcrestdetailing
Facebook: facebook.com/brightcrestdetailing

Requirements
Must have
• Business name, my name, address, phone number. Listing that I do minor paint correction such as clay barring, multi-step buffing and polishing, waxing, hand washes, interior cleaning, and more. (This last part was in nice to haves but I have realized that I do really want it, so I moved it to must haves.) I want something that is different and eye-catching to my customers. Some people have done this very well with cards already submitted to me, but a lot have not. I didn't mess with the "look and feel bars" much because because I am pretty open to the overall design as long as it is not your basic run of the mill design.
Nice to have
• Something car related. Maybe an appointment time/date line. I do not have a logo, but if you would like to design one and incorporate it, that would be amazing!
Should not have
• Purple and Pink colors. Boring, basic, normal card.

```html
<!DOCTYPE html>
<html lang="en">
<head>
<meta charset="utf-8">
<title>Bright Crest Detailing – Business Card</title>
<link rel="stylesheet" href="https://fonts.googleapis.com/css2?family=Tinos:wght@400;700&display=swap">
<style>
  :root {
    --page-bg: #e9e6e1;
    --card-bg: #ffffff;
    --brand-blue: #2a4f9f;
    --text-grey: #6a6a6a;
    --dot-grey: #9a9a9a;
    --rule-blue: #9fb3d9;
    --shadow: rgba(0, 0, 0, 0.18);
  }
  * { box-sizing: border-box; margin: 0; padding: 0; }
  html, body {
    width: 1200px;
    height: 950px;
    overflow: hidden;
    background: var(--page-bg);
    font-family: "Tinos", "Times New Roman", serif;
  }
  .sheet {
    width: 1200px;
    height: 950px;
    display: flex;
    flex-direction: column;
    align-items: center;
    justify-content: center;
    gap: 56px;
  }
  .card {
    position: relative;
    width: 640px;
    height: 366px;
    background: var(--card-bg);
    box-shadow: 0 10px 28px var(--shadow);
  }

  /* Front */
  .brand-name {
    position: absolute;
    top: 92px;
    left: 0;
    width: 100%;
    text-align: center;
    color: var(--brand-blue);
    font-size: 44px;
    font-weight: 400;
    letter-spacing: 1px;
  }
  .appt-line {
    position: absolute;
    display: flex;
    align-items: baseline;
    color: var(--brand-blue);
    font-size: 17px;
  }
  .appt-line .fill {
    display: inline-block;
    border-bottom: 2px dotted var(--dot-grey);
    margin: 0 6px;
    height: 1px;
  }
  .appt-time { top: 188px; left: 280px; }
  .appt-time .fill { width: 150px; }
  .appt-time .suffix { font-size: 12px; }
  .appt-date { top: 262px; left: 52px; }
  .appt-date .fill { width: 290px; }

  /* Back */
  .holder-name {
    position: absolute;
    top: 78px;
    width: 100%;
    text-align: center;
    color: var(--brand-blue);
    font-size: 27px;
  }
  .rule {
    position: absolute;
    left: 60px;
    width: 520px;
    height: 1px;
    background: linear-gradient(90deg, transparent, var(--rule-blue), transparent);
  }
  .rule-top { top: 122px; }
  .rule-bottom { top: 238px; }
  .contact-list {
    position: absolute;
    top: 134px;
    width: 100%;
    list-style: none;
    text-align: center;
    color: var(--text-grey);
    font-size: 15px;
    line-height: 30px;
  }
  .contact-item { display: inline-flex; align-items: center; margin: 0 6px; }
  .contact-item svg { width: 14px; height: 14px; margin-right: 4px; fill: var(--brand-blue); }
  .services {
    position: absolute;
    top: 256px;
    width: 100%;
    text-align: center;
    color: var(--text-grey);
    font-size: 15.5px;
    line-height: 24px;
  }
</style>
</head>
<body>
<main class="sheet">

  <section class="card card-front" aria-label="Card front">
    <h1 class="brand-name">Bright Crest Detailing</h1>
    <div class="appt-line appt-time">Time :<span class="fill"></span><span class="suffix">AM/PM</span></div>
    <div class="appt-line appt-date">Date :<span class="fill"></span></div>
  </section>

  <section class="card card-back" aria-label="Card back">
    <h2 class="holder-name">Mira Tolland</h2>
    <div class="rule rule-top"></div>
    <ul class="contact-list">
      <li>
        <span class="contact-item">
          <svg viewBox="0 0 24 24" aria-hidden="true"><path d="M12 2a7 7 0 0 0-7 7c0 5.2 7 13 7 13s7-7.8 7-13a7 7 0 0 0-7-7zm0 9.5A2.5 2.5 0 1 1 12 6.5a2.5 2.5 0 0 1 0 5z"/></svg>
          4175 Quenhollow Rd, Ashmere PA 17492
        </span>
      </li>
      <li>
        <span class="contact-item">
          <svg viewBox="0 0 24 24" aria-hidden="true"><path d="M7 1h10a2 2 0 0 1 2 2v18a2 2 0 0 1-2 2H7a2 2 0 0 1-2-2V3a2 2 0 0 1 2-2zm0 3v15h10V4H7zm5 16.2a1 1 0 1 0 0 .1z"/></svg>
          717-555-0148
        </span>
        <span class="contact-item">
          <svg viewBox="0 0 24 24" aria-hidden="true"><path d="M2 5h20v14H2V5zm2 2v.5l8 5.5 8-5.5V7H4zm0 3v7h16v-7l-8 5.5L4 10z"/></svg>
          brightcrestdetails@maildrop-example.com
        </span>
      </li>
      <li>
        <span class="contact-item">
          <svg viewBox="0 0 24 24" aria-hidden="true"><rect x="3" y="3" width="18" height="18" rx="3"/></svg>
          @brightcrestdetailing
        </span>
      </li>
    </ul>
    <div class="rule rule-bottom"></div>
    <p class="services">Minor paint correction such as clay barring<br>multi-step buffing &amp; polishing | waxing | hand washes, etc.</p>
  </section>

</main>
</body>
</html>
```